New banner graphics for Tondix.com website

I've developed a software tool that helps businesses ensure they are working on their most valuable and important work.

I would like a banner graphic for my home page (www.tondix.com) that can somehow capture the value of focus and intentional outcomes.

I had an initial thought of a starry sky that shifts focus to a few bright stars, but while that might sound ok, I think my idea is lame hence I'm coming to you guys.

My sites two primary colors are a soft purple and gray.
#919EC1(purple)
#9E9E9E (gray)

Target Market(s)

B2B for enterprises. Typical customers are CFOs, CIOs/Heads of IT

Industry/Entity Type

Business Software

Number of Pages Required

1 page

Font styles to use
Sans Serif

Colors
b8a6cd
cedeed

Requirements
Must have
• I use Divi as my Wordpress theme and the current main landing page can be seen at www.tondix.com.
• My logo colors are:
• #919EC1(purple)
• #9E9E9E (gray)
Should not have
• Lots of distraction or visual "noise". I want to re-enforce the message that my software is focused on their business and not my products or website.

```html
<!DOCTYPE html>
<html lang="en">
<head>
<meta charset="utf-8">
<title>Tondix — Waypoint</title>
<link rel="stylesheet" href="https://fonts.googleapis.com/css2?family=Montserrat:wght@400;500;600;700&family=Open+Sans:wght@400;600;700&family=Crimson+Text:ital@1&display=swap">
<style>
  :root{
    --navy:#0d0c47;
    --search:#a8a7ea;
    --go:#1fc21f;
    --red:#c0141c;
    --brand-purple:#919ec1;
    --brand-gray:#9e9e9e;
    --stone:#b9b3b3;
    --footer:#424242;
    --yellow:#eaea4c;
    --ink:#111;
    --white:#fff;
    --social:#6f7fb8;
  }
  *{box-sizing:border-box;margin:0;padding:0}
  html,body{width:720px;height:1200px;overflow:hidden}
  body{position:relative;background:var(--white);font-family:"Montserrat",sans-serif;color:var(--ink)}
  .abs{position:absolute}

  .site-header{left:0;top:0;width:720px;height:49px;background:var(--navy)}
  .brand{left:71px;top:8px;font-family:"Montserrat",sans-serif;font-weight:400;font-size:26px;color:#b7b7c7;letter-spacing:-.5px}
  .search{left:234px;top:24px;width:214px;height:17px;background:var(--search);font-size:8px;line-height:17px;padding-left:37px;color:#222;font-family:"Open Sans",sans-serif}
  .search-go{left:448px;top:24px;width:33px;height:17px;background:var(--go)}
  .social-top{left:533px;top:22px;display:flex;gap:4px}
  .social-dot{width:20px;height:20px;border-radius:50%;background:var(--social)}

  .nav{left:0;top:49px;width:720px;height:21px;font-family:"Open Sans",sans-serif;font-size:10px;color:var(--red)}
  .nav span{position:absolute;top:5px}

  .hero{left:0;top:70px;width:720px;height:240px;background:linear-gradient(180deg,#1b2140 0%,#2a3357 45%,#1a1e38 100%)}
  .hero-title{left:160px;top:82px;width:400px;text-align:center;color:var(--white);font-weight:500;font-size:20px;line-height:22px}
  .video{left:267px;top:150px;width:175px;height:116px;border:2px solid #ddd;border-radius:8px;background:linear-gradient(120deg,#555 0%,#222 45%,#000 55%,#222 100%);overflow:hidden}
  .video-caption{position:absolute;left:2px;top:20px;font-family:"Open Sans",sans-serif;font-size:10px;color:var(--white)}
  .video-caption b{color:#151573}
  .video-play{position:absolute;left:52px;top:18px}
  .video-name{position:absolute;left:0;width:100%;top:82px;text-align:center;font-size:13px;color:#aaa}
  .cta{left:248px;top:276px;width:202px;height:30px;background:var(--brand-gray);text-align:center;line-height:30px;font-weight:700;font-size:15px;color:var(--ink)}

  .pillars{left:0;top:310px;width:720px;height:49px;background:var(--brand-gray);font-family:"Open Sans",sans-serif;font-weight:600;font-size:11px;color:var(--yellow)}
  .pillar{position:absolute;display:flex;align-items:center;gap:5px}
  .pillar::before{content:"";width:10px;height:10px;border-radius:50%;background:#000}

  .diff-title{left:0;top:374px;width:720px;text-align:center;font-weight:600;font-size:15px}
  .card{top:418px;width:127px;height:190px;background:var(--brand-purple);border:2px solid #8a8a8a;border-radius:12px;padding:26px 6px 0 6px;font-size:10.2px;line-height:12.2px;color:#111}
  .card-icon{top:401px;width:43px;height:43px;border-radius:50%;background:var(--white);border:2px solid #888;display:flex;align-items:center;justify-content:center}

  .proof{left:0;top:626px;width:720px;height:425px;background:var(--stone)}
  .chart{background:var(--white);border:2px solid #555}
  .chart-title{position:absolute;left:6px;top:3px;font-size:5px;font-family:"Open Sans",sans-serif}

  .testi-title{left:0;top:892px;width:720px;text-align:center;font-weight:600;font-size:15px}
  .quote{font-family:"Crimson Text",serif;font-style:italic;font-size:8px;line-height:14.5px;left:187px;top:913px;width:334px;text-align:center;color:#222}
  .quote-mark{font-family:"Montserrat",sans-serif;font-weight:700;font-size:70px;color:var(--white);line-height:1}
  .dots{left:343px;top:952px;display:flex;gap:4px}
  .dots i{width:4px;height:4px;border-radius:50%;background:#111}
  .dots i.on{background:#6c6}
  .portrait{top:959px;width:90px;height:90px;border-radius:50%;border:2px solid #333}
  .portrait-name{position:absolute;left:0;width:100%;top:65px;text-align:center;font-family:"Crimson Text",serif;font-style:italic;font-size:11px;color:#111}

  .footer{left:0;top:1051px;width:720px;height:149px;background:var(--footer);color:var(--white);text-align:center}
  .social-foot{position:absolute;left:299px;top:52px;display:flex;gap:5px}
  .social-foot .social-dot{width:20px;height:20px}
  .footer-links{position:absolute;left:0;width:100%;top:92px;font-size:12.5px}
  .copyright{position:absolute;left:0;width:100%;top:127px;font-size:9px}
</style>
</head>
<body>

<header class="site-header abs">
  <div class="brand abs">Tondix</div>
  <div class="search abs">Enter your search keyword...</div>
  <div class="search-go abs">
    <svg width="33" height="17" viewBox="0 0 33 17"><circle cx="15" cy="7.5" r="4" fill="none" stroke="#000" stroke-width="1.3"/><line x1="18" y1="10.5" x2="21" y2="13.5" stroke="#000" stroke-width="1.3"/></svg>
  </div>
  <div class="social-top abs">
    <span class="social-dot"></span><span class="social-dot"></span><span class="social-dot"></span><span class="social-dot"></span><span class="social-dot"></span>
  </div>
</header>

<nav class="nav abs">
  <span style="left:71px">Request a Demo</span>
  <span style="left:186px">Links</span>
</nav>

<section class="hero abs" role="img" aria-label="Night city skyline, softly out of focus"></section>
<h1 class="hero-title abs">A simple software tool that makes your business goals actionable.</h1>
<div class="video abs">
  <div class="video-caption">Give <b>Waypoint</b> a try for free today</div>
  <svg class="video-play" width="70" height="70" viewBox="0 0 70 70"><circle cx="35" cy="35" r="32" fill="none" stroke="#666" stroke-width="4"/><polygon points="27,20 52,35 27,50" fill="#666"/></svg>
  <div class="video-name">Tondix</div>
  <svg style="position:absolute;left:12px;top:102px" width="148" height="6" viewBox="0 0 148 6"><rect x="0" y="2" width="148" height="2" fill="#bbb"/><rect x="0" y="2" width="110" height="2" fill="#e33"/><circle cx="62" cy="3" r="2.5" fill="#fff"/></svg>
</div>
<div class="cta abs">START FREE DEMO</div>

<section class="pillars abs">
  <span class="pillar" style="left:87px;top:8px">Define the outcomes</span>
  <span class="pillar" style="left:228px;top:8px;color:#e0e07a;font-weight:400">Set the Direction</span>
  <span class="pillar" style="left:363px;top:8px">Focus the Resources</span>
  <span class="pillar" style="left:510px;top:8px">Reduce the Risk</span>
  <span class="pillar" style="left:285px;top:29px">Increase Team Engagement</span>
</section>

<h2 class="diff-title abs">What Makes Waypoint Different?</h2>

<div class="card abs" style="left:70px">We want you to spend time thinking about and planning for your organization's success, not learning yet another tool. Waypoint has a modern UI making it more intuitive.</div>
<div class="card abs" style="left:219px">We want you to spend time thinking about and planning for your organization's success, not learning yet another tool. Waypoint has a modern UI making it more intuitive.</div>
<div class="card abs" style="left:369px">We want you to spend time thinking about and planning for your organization's success, not learning yet another tool. Waypoint has a modern UI making it more intuitive.</div>
<div class="card abs" style="left:519px">We want you to spend time thinking about and planning for your organization's success, not learning yet another tool. Waypoint has a modern UI making it more intuitive.</div>

<div class="card-icon abs" style="left:113px">
  <svg width="20" height="28" viewBox="0 0 20 28"><rect x="2" y="1" width="16" height="26" rx="3" fill="none" stroke="#7f8cb8" stroke-width="2"/><line x1="7" y1="23" x2="13" y2="23" stroke="#7f8cb8" stroke-width="2"/></svg>
</div>
<div class="card-icon abs" style="left:261px">
  <svg width="28" height="24" viewBox="0 0 28 24"><line x1="14" y1="2" x2="14" y2="21" stroke="#7f8cb8" stroke-width="2"/><line x1="4" y1="6" x2="24" y2="4" stroke="#7f8cb8" stroke-width="2"/><path d="M1 14 L5 6 L9 14 Z" fill="#7f8cb8"/><path d="M19 12 L23 4 L27 12 Z" fill="#7f8cb8"/><line x1="9" y1="22" x2="19" y2="22" stroke="#7f8cb8" stroke-width="2"/></svg>
</div>
<div class="card-icon abs" style="left:411px">
  <svg width="30" height="30" viewBox="0 0 30 30"><circle cx="15" cy="15" r="13" fill="none" stroke="#7f8cb8" stroke-width="2.5"/><circle cx="15" cy="15" r="8" fill="none" stroke="#7f8cb8" stroke-width="2.5"/><circle cx="15" cy="15" r="3.5" fill="#7f8cb8"/></svg>
</div>
<div class="card-icon abs" style="left:561px">
  <svg width="30" height="30" viewBox="0 0 30 30"><rect x="3" y="9" width="14" height="7" rx="3.5" transform="rotate(45 10 12)" fill="none" stroke="#7f8cb8" stroke-width="2"/><rect x="13" y="15" width="14" height="7" rx="3.5" transform="rotate(45 20 18)" fill="none" stroke="#7f8cb8" stroke-width="2"/></svg>
</div>

<section class="proof abs"></section>

<div class="chart abs" style="left:209px;top:647px;width:312px;height:115px">
  <span class="chart-title">Project Cost Breakdown</span>
  <svg class="abs" style="left:0;top:0" width="308" height="111" viewBox="0 0 308 111">
    <line x1="40" y1="22" x2="40" y2="108" stroke="#444" stroke-width=".6"/>
    <line x1="40" y1="108" x2="300" y2="108" stroke="#888" stroke-width=".6"/>
    <g font-size="3" font-family="Open Sans" fill="#333">
      <text x="16" y="30">$1,200,000</text><text x="16" y="44">$1,000,000</text><text x="16" y="58">$800,000</text><text x="16" y="72">$600,000</text><text x="16" y="86">$400,000</text><text x="16" y="100">$200,000</text>
    </g>
    <rect x="50" y="33" width="23" height="30" fill="#f00"/><rect x="50" y="63" width="23" height="45" fill="#00f"/>
    <rect x="89" y="60" width="23" height="7" fill="#f00"/><rect x="89" y="67" width="23" height="41" fill="#00f"/>
    <rect x="128" y="86" width="23" height="5" fill="#f00"/><rect x="128" y="91" width="23" height="17" fill="#00f"/>
    <rect x="167" y="124" width="0" height="0"/>
    <rect x="167" y="99" width="23" height="3" fill="#f00"/><rect x="167" y="102" width="23" height="6" fill="#00f"/>
    <rect x="206" y="101" width="23" height="4" fill="#f00"/><rect x="206" y="105" width="23" height="3" fill="#00f"/>
    <rect x="245" y="102" width="23" height="2" fill="#f00"/><rect x="245" y="104" width="23" height="4" fill="#00f"/>
    <rect x="284" y="104" width="23" height="1.5" fill="#f00"/><rect x="284" y="105.5" width="23" height="2.5" fill="#00f"/>
    <rect x="268" y="22" width="34" height="13" fill="#fff" stroke="#ccc" stroke-width=".4"/>
    <rect x="271" y="25" width="3" height="3" fill="#00f"/><text x="276" y="28" font-size="3.2" font-family="Open Sans">External Cost</text>
    <rect x="271" y="30" width="3" height="3" fill="#f00"/><text x="276" y="33" font-size="3.2" font-family="Open Sans">Internal Cost</text>
  </svg>
</div>

<div class="chart abs" style="left:210px;top:770px;width:312px;height:114px">
  <span class="chart-title">Strategic Value Summary</span>
  <svg class="abs" style="left:0;top:0" width="308" height="110" viewBox="0 0 308 110">
    <line x1="22" y1="18" x2="22" y2="104" stroke="#444" stroke-width=".6"/>
    <line x1="22" y1="104" x2="300" y2="104" stroke="#444" stroke-width=".6"/>
    <line x1="22" y1="66" x2="290" y2="66" stroke="#999" stroke-width=".5"/>
    <circle cx="39" cy="48" r=".8" fill="#999"/>
    <circle cx="93" cy="58" r="1.3" fill="#999"/>
    <circle cx="108" cy="50" r="1.6" fill="#999"/>
    <circle cx="56" cy="63" r=".8" fill="#999"/>
    <circle cx="220" cy="50" r="10" fill="#e89ad6" opacity=".9"/>
    <circle cx="205" cy="50" r="7.5" fill="#e07a8a" opacity=".9"/>
    <circle cx="309" cy="49" r="0" fill="none"/>
    <circle cx="285" cy="49" r="5" fill="#73acd6"/>
    <text x="250" y="106" font-size="3" font-family="Open Sans">Duration in months</text>
  </svg>
</div>

<h2 class="testi-title abs">Testimonials</h2>
<span class="quote-mark abs" style="left:140px;top:897px">“</span>
<p class="quote abs">This is a sample testimonial for the site. Proin gravida nibh vel velit auctor aliquet. Aenean sollicitudin, lorem quis bibendum auctor, nisi elit consequat ipsum, nec sagittis sem nibh id elit. Duis sed odio sit amet nibh vulputate cursus a sit amet mauris. Morbi accumsan ipsum velit. Nam nec tellus</p>
<span class="quote-mark abs" style="left:526px;top:918px">”</span>
<div class="dots abs"><i></i><i class="on"></i><i></i></div>

<div class="portrait abs" role="img" aria-label="Customer portrait photo, black and white" style="left:210px;background:radial-gradient(circle at 50% 45%,#9a9a9a,#3c3c3c)"></div>
<div class="portrait abs" role="img" aria-label="Customer portrait photo, outdoors" style="left:313px;background:linear-gradient(180deg,#6a5a48 0%,#8a6d55 55%,#5e9a4a 75%,#4f8a3e 100%)"><span class="portrait-name">Daniel M.</span></div>
<div class="portrait abs" role="img" aria-label="Customer portrait photo, black and white" style="left:416px;background:radial-gradient(circle at 50% 45%,#b0b0b0,#444)"></div>

<footer class="footer abs">
  <div class="social-foot">
    <span class="social-dot"></span><span class="social-dot"></span><span class="social-dot"></span><span class="social-dot"></span><span class="social-dot"></span><span class="social-dot" style="background:#e67e22"></span>
  </div>
  <div class="footer-links">Resources Chronicles Support FAQ Terms of Service Pricing About</div>
  <div class="copyright">Copyright (c) 2017 www.tondix.com All Rights Reserved</div>
</footer>

</body>
</html>
```